Website Design for a Project Management Consulting Business

I have a logo design already and now I need a website.
I am a project manager and run my own consulting business.
Currently I am under contract with 3 major Vantage 400 companies. I'd like a website I can direct current and future clients.
My job is running IT projects and working with developers to deliver business priorities.
The website should be professional and clean - I work IT projects and would like to incorporate that into any theme.
I'd like the site to have several page or breakoff links - sections would include : about me, about my services, a page to display all of my certification badges, another page to talk about highlights from past projects and so on.
Looking for a collaborative experience.

Industry/Entity Type

Vantage 400 Consulting Firm - Project Management

Coding

Coded - Design and coding required

Number of Pages Required

1 page

Font styles to use
Serif

Colors
0094D4
00A9DD
6FCCEA
C7EBF8
E9F6FB
EE7325
F08F49
F5BC92
FAE3D3
FDF4ED

Requirements
Must have
• Sections that are a must: About Me (bio), About My Services, About my Certifications and Credentials, Experience on Past Projects,
Nice to have
• I have added the logo below - I'd like to use the logo and have it prominent ; should be professional and inviting

```html
<!DOCTYPE html>
<html lang="en">
<head>
<meta charset="utf-8">
<title>Meridian Project Partners – Project Management Consulting</title>
<link href="https://fonts.googleapis.com/css2?family=Orbitron:wght@600;700&family=Roboto:wght@400;500;700&display=swap" rel="stylesheet">
<style>
:root{
  --navy:#0b3566;
  --navy-deep:#062a55;
  --blue:#0094d4;
  --blue-mid:#00a9dd;
  --blue-soft:#6fccea;
  --blue-pale:#c7ebf8;
  --blue-wash:#e6f3f9;
  --orange:#ee7325;
  --orange-mid:#f08f49;
  --orange-soft:#f5bc92;
  --text:#555b63;
  --ink:#1d1f22;
  --white:#ffffff;
}
*{margin:0;padding:0;box-sizing:border-box}
html,body{width:1200px;height:3620px;overflow:hidden;background:var(--white)}
body{font-family:"Roboto",Arial,sans-serif;color:var(--text)}
.page{position:relative;width:1200px;height:3620px;overflow:hidden}
.abs{position:absolute}
.display{font-family:"Orbitron","Arial Black",sans-serif;font-weight:700;color:var(--navy);letter-spacing:1px}
.btn{position:absolute;background:var(--orange);color:var(--white);font-family:"Roboto",Arial,sans-serif;font-weight:500;text-transform:uppercase;display:flex;align-items:center;justify-content:center;font-size:14px}
.btn-small{font-size:11.5px}

/* header */
.topbar{left:0;top:0;width:1200px;height:5px;background:var(--blue)}
.brand{left:147px;top:22px;display:flex;align-items:center;gap:10px}
.brand-square{width:34px;height:34px;border:3px solid var(--navy)}
.brand-name{font-family:"Orbitron",sans-serif;font-weight:700;font-size:19px;color:var(--navy);letter-spacing:.5px}
.nav{left:435px;top:35px;display:flex;gap:32px;font-size:12.5px;font-weight:500;color:var(--ink);text-transform:uppercase}
.nav .home{display:flex;align-items:center;gap:6px}
.nav .home i{display:block;width:13px;height:13px;border:1.5px solid var(--blue)}
.rule-blue{left:0;top:82px;width:565px;height:5px;background:var(--blue)}
.rule-navy{left:565px;top:84px;width:635px;height:3px;background:var(--navy)}

/* hero */
.hero-side{left:0;top:88px;width:142px;height:526px;background:linear-gradient(180deg,#0a2c52,#0d4a84 60%,#092b52)}
.hero-panel{left:142px;top:88px;width:423px;height:526px;background:var(--blue)}
.hero-photo{left:565px;top:88px;width:635px;height:526px;background:radial-gradient(ellipse at 85% 85%,#d9dde4 0,#5b7fb8 22%,#1f5fc2 45%,#0d48a8 75%,#0a3d8f 100%)}
.hero-title{left:170px;top:342px;font-size:35px;line-height:43px;color:var(--white);letter-spacing:1px}
.dots-slider{left:72px;top:324px}
.dots-slider span{display:block;width:8px;height:8px;border-radius:50%;background:var(--white);margin-bottom:12px}
.dots-slider span.on{background:var(--blue-mid)}

/* section headings */
.heading{left:0;width:1200px;display:flex;align-items:center;justify-content:center;gap:20px;font-size:35px;white-space:nowrap}
.heading::before,.heading::after{content:"";display:block;width:76px;height:2px;background:var(--navy);flex:none}
.heading.stack{line-height:44px;text-align:center}
.heading.about{left:600px;width:411px;font-size:34px;line-height:40px;gap:18px}
.heading.about::before,.heading.about::after{width:60px}

/* services */
.card{position:absolute;width:221px;height:266px;background:var(--white);border:2px solid #e5e8ec;text-align:center;box-shadow:0 2px 6px rgba(0,0,0,.03)}
.card.active{border-color:var(--navy);box-shadow:0 8px 20px rgba(11,53,102,.18)}
.card-tab{position:absolute;left:70px;top:-26px;width:78px;height:66px;background:var(--navy);border-radius:0 66px 0 0}
.card-tab i{position:absolute;left:19px;top:14px;width:30px;height:30px;border:2px solid var(--white);border-radius:50%}
.card h3{position:absolute;left:0;width:100%;top:70px;font-size:18px;line-height:25px;font-weight:500;color:var(--ink);text-transform:uppercase}
.card p{position:absolute;left:26px;right:26px;font-size:12.5px;line-height:24px;color:#444}
.card .btn{left:61px;bottom:-18px;width:98px;height:36px}
.dotgrid{display:grid;gap:0}
.dotgrid span{width:4px;height:4px;border-radius:50%;background:var(--blue-mid)}

/* about */
.about-band{left:0;top:1248px;width:1200px;height:592px;background:var(--blue-wash)}
.about-frame{left:144px;top:1452px;width:402px;height:288px;background:var(--blue)}
.about-arch{left:180px;top:1358px;width:170px;height:290px;background:var(--navy);border-radius:0 170px 0 0;border-top:6px solid var(--white);border-left:6px solid var(--white)}
.about-photo{left:195px;top:1352px;width:351px;height:388px;background:linear-gradient(180deg,rgba(143,154,172,.55) 0,#6d84a6 45%,#54698a 100%)}
.about-text{left:600px;top:1455px;width:456px;font-size:12.5px;line-height:24px;color:var(--text);text-align:justify}

/* projects */
.tile{position:absolute}
.t1{left:146px;top:2041px;width:252px;height:295px;background:linear-gradient(135deg,#c9c6c0,#8a6a4d 45%,#3b3936)}
.t2{left:411px;top:2041px;width:253px;height:295px;background:linear-gradient(160deg,#c9ced2,#8b9197 50%,#2e3338)}
.t3{left:677px;top:2041px;width:378px;height:295px;background:linear-gradient(135deg,#a85a2a,#e39a63 45%,#f2c8a2)}
.t4{left:146px;top:2350px;width:377px;height:295px;background:linear-gradient(150deg,#e9ecee,#a69a8c 50%,#5e4f42)}
.t5{left:536px;top:2350px;width:253px;height:295px;background:linear-gradient(150deg,#4f5a66,#1f2a36 60%,#2c3642)}
.t6{left:802px;top:2350px;width:253px;height:295px;background:linear-gradient(150deg,#9fa7ae,#3f4a55 50%,#6b5a48)}
.zoom{left:853px;top:2175px;width:27px;height:27px;border-radius:50%;background:var(--blue-mid)}

/* certifications */
.cert-bg{left:0;top:2650px;width:1200px;height:590px;background:radial-gradient(circle at 70px 240px,#dbe3ea 0,#f0f4f7 180px,#ffffff 420px)}
.badge{position:absolute;width:226px;height:226px;border-radius:50%}
.badge.gold{background:radial-gradient(circle,#ffc21a 0 58%,#ffffff 58% 62%,#f9b51b 62% 100%)}
.badge.orange{background:radial-gradient(circle,#f26a2c 0 58%,#ffffff 58% 62%,#ef5a23 62% 100%)}
.chev{position:absolute;width:30px;height:30px;border-left:1.5px solid #8d96a0;border-bottom:1.5px solid #8d96a0}

/* footer */
.footer-bg{left:0;top:3240px}
.fcol{position:absolute;top:3318px;color:var(--white)}
.fcol h4{font-family:"Orbitron",sans-serif;font-weight:600;font-size:14.5px;letter-spacing:.5px;text-transform:uppercase}
.fcol h4::after{content:"";display:block;width:24px;height:3px;background:var(--blue-mid);margin-top:12px}
.fcol ul{list-style:none;margin-top:19px}
.fcol li{font-size:12.5px;line-height:25.5px}
.fcol p{font-size:12.5px;margin-top:20px}
.news-form{display:flex;margin-top:20px}
.news-input{width:170px;height:37px;background:var(--white);color:#333;font-size:11px;display:flex;align-items:center;padding-left:16px}
.news-btn{position:static;width:78px;height:37px;font-size:13.5px;font-weight:700}
.copyright{left:181px;top:3548px;font-size:12.5px;color:var(--white)}
.social{top:3546px;width:18px;height:18px;border-radius:50%;background:var(--white)}
</style>
</head>
<body>
<div class="page">

  <!-- header -->
  <div class="abs topbar"></div>
  <div class="abs brand"><span class="brand-square"></span><span class="brand-name">MERIDIAN PM</span></div>
  <nav class="abs nav">
    <span class="home"><i></i>Home</span>
    <span>About Me</span>
    <span>Services</span>
    <span>Certifications and Credentials</span>
    <span>Past Projects</span>
  </nav>
  <div class="abs rule-blue"></div>
  <div class="abs rule-navy"></div>

  <!-- hero -->
  <section>
    <div class="abs hero-side" role="img" aria-label="Blurred dark blue background"></div>
    <div class="abs hero-panel"></div>
    <svg class="abs" style="left:142px;top:88px" width="423" height="526" viewBox="0 0 423 526" aria-hidden="true">
      <path d="M8 136 C120 100 300 150 368 330 C388 390 392 460 388 520 H8 Z" fill="#0b3566"/>
      <path d="M8 128 C120 92 302 142 376 326 C396 386 400 460 396 526" fill="none" stroke="#ffffff" stroke-width="7"/>
    </svg>
    <div class="abs hero-photo" role="img" aria-label="Photo of a blue dart hitting the centre of a dartboard"></div>
    <div class="abs dots-slider"><span></span><span class="on"></span><span></span></div>
    <h1 class="abs display hero-title">PROJECT<br>MANAGEMENT<br>CONSULTING<br>BUSINESS</h1>
    <div class="btn" style="left:171px;top:536px;width:119px;height:43px">Read More</div>
  </section>

  <!-- services -->
  <section>
    <h2 class="abs display heading" style="top:700px">MY SERVICES</h2>

    <div class="card" style="left:145px;top:845px">
      <div class="card-tab"><i></i></div>
      <h3>Consulting</h3>
      <p style="top:106px">Lorem ipsum dolor sit amet, consectetur adipiscing elit, sed do eiusmod tempor incididunt ut labodolore magna aliqua</p>
      <div class="btn btn-small">Read More</div>
    </div>
    <div class="card active" style="left:375px;top:877px">
      <div class="card-tab"><i></i></div>
      <h3>Project<br>Management</h3>
      <p style="top:130px">Lorem ipsum dolor sit amet, consectetur adipiscing elit, sed do eiusmod tempor incididunt ut labod</p>
      <div class="btn btn-small">Read More</div>
    </div>
    <div class="card" style="left:604px;top:845px">
      <div class="card-tab"><i></i></div>
      <h3>Itae Dicta Sun</h3>
      <p style="top:106px">Lorem ipsum dolor sit amet, consectetur adipiscing elit, sed do eiusmod tempor incididunt ut labodolore magna aliqua</p>
      <div class="btn btn-small">Read More</div>
    </div>
    <div class="card" style="left:836px;top:877px">
      <div class="card-tab"><i></i></div>
      <h3>Eius Modi Tem</h3>
      <p style="top:106px">Lorem ipsum dolor sit amet, consectetur adipiscing elit, sed do eiusmod tempor incididunt ut labodolore magna aliqua</p>
      <div class="btn btn-small">Read More</div>
    </div>

    <div class="abs dotgrid" style="left:428px;top:1154px;grid-template-columns:repeat(6,4px);column-gap:19px;row-gap:18px">
      <span></span><span></span><span></span><span></span><span></span><span></span>
      <span></span><span></span><span></span><span></span><span></span><span></span>
    </div>
  </section>

  <!-- about -->
  <section>
    <div class="abs about-band"></div>
    <div class="abs dotgrid" style="left:54px;top:1451px;grid-template-columns:repeat(4,4px);column-gap:19px;row-gap:18px">
      <span></span><span></span><span></span><span></span><span></span><span></span><span></span><span></span>
      <span></span><span></span><span></span><span></span><span></span><span></span><span></span><span></span>
      <span></span><span></span><span></span><span></span>
    </div>
    <div class="abs about-frame"></div>
    <div class="abs about-arch"></div>
    <div class="abs about-photo" role="img" aria-label="Portrait photo of the consultant in a blue checked suit and tie"></div>
    <h2 class="abs display heading about" style="top:1388px">ABOUT ME</h2>
    <p class="abs about-text">Marcus Delaney is the Owner of Meridian Project Partners, LLC and serves as Principal Lead Consultant on waterfall and agile contract opportunities. Meridian Project Partners, LLC has engaged on a contract basis with Vantage 400 companies across various industries including banking and credit unions, global supply chain, and international food distribution. Marcus brings 12 years of experience to his clients encompassing various project methodologies including: waterfall, agile, and hybrid frameworks. Most recently, Meridian Project Partners, LLC has took on PM consulting contracts in the agile transformation space.</p>
    <div class="btn" style="left:600px;top:1697px;width:118px;height:43px">Read More</div>
    <div class="abs dotgrid" style="left:1072px;top:1784px;grid-template-columns:repeat(6,4px);column-gap:19px;row-gap:18px">
      <span></span><span></span><span></span><span></span><span></span><span></span>
      <span></span><span></span><span></span><span></span><span></span><span></span>
      <span></span><span></span><span></span><span></span><span></span><span></span>
      <span></span><span></span><span></span><span></span><span></span><span></span>
      <span></span><span></span><span></span><span></span><span></span><span></span>
    </div>
  </section>

  <!-- past projects -->
  <section>
    <h2 class="abs display heading" style="top:1931px">PAST PROJECTS</h2>
    <div class="tile t1" role="img" aria-label="Photo of colleagues reviewing work at a computer"></div>
    <div class="tile t2" role="img" aria-label="Photo of a team meeting in front of a whiteboard diagram"></div>
    <div class="tile t3" role="img" aria-label="Photo of hands reviewing financial charts, orange toned"></div>
    <div class="abs zoom"></div>
    <div class="tile t4" role="img" aria-label="Photo of a business team meeting around a table"></div>
    <div class="tile t5" role="img" aria-label="Photo of a laptop with digital interface overlay"></div>
    <div class="tile t6" role="img" aria-label="Photo of two people discussing a tablet"></div>
  </section>

  <!-- certifications -->
  <section>
    <div class="abs cert-bg" role="img" aria-label="Faint photo of darts in a target"></div>
    <div class="btn" style="left:541px;top:2706px;width:118px;height:42px">Load More</div>
    <h2 class="abs display heading stack" style="top:2832px">CERTIFICATIONS AND<br>CREDENTIALS</h2>
    <div class="chev" style="left:156px;top:3060px;transform:rotate(45deg)"></div>
    <div class="badge gold" style="left:209px;top:2962px" role="img" aria-label="Certification badge"></div>
    <div class="badge orange" style="left:487px;top:2962px" role="img" aria-label="Certification badge"></div>
    <div class="badge gold" style="left:767px;top:2962px" role="img" aria-label="Certification badge"></div>
    <div class="chev" style="left:1014px;top:3060px;transform:rotate(-135deg)"></div>
  </section>

  <!-- footer -->
  <footer>
    <svg class="abs footer-bg" width="1200" height="380" viewBox="0 0 1200 380" aria-hidden="true">
      <path d="M0 0 H720 C960 0 1170 150 1200 380 H0 Z" fill="#0b3566"/>
    </svg>
    <div class="fcol" style="left:181px">
      <h4>Useful Links</h4>
      <ul><li>Upcoming Courses</li><li>Training</li><li>Consulting</li><li>Blogs</li></ul>
    </div>
    <div class="fcol" style="left:396px">
      <h4>About</h4>
      <ul><li>About</li><li>Our Team</li><li>Our Approach</li><li>Testimonials</li></ul>
    </div>
    <div class="fcol" style="left:568px">
      <h4>Policies</h4>
      <ul><li>Privacy Policy</li><li>Terms and Conditions</li><li>Cookie Policy</li><li>Contact Us</li></ul>
    </div>
    <div class="fcol" style="left:770px">
      <h4>Newsletter</h4>
      <p>Sed ut perspiciatis unde omnis iste natus</p>
      <div class="news-form">
        <div class="news-input">Enter Email</div>
        <div class="btn news-btn">Sign Up</div>
      </div>
    </div>
    <p class="abs copyright">copyright © 2022 Meridian Project Partners.All Rights Reserved</p>
    <span class="abs social" style="left:894px" aria-label="Social link"></span>
    <span class="abs social" style="left:947px" aria-label="Social link"></span>
    <span class="abs social" style="left:1000px" aria-label="Social link"></span>
  </footer>

</div>
</body>
</html>
```